Brivane Management

We need a web design for a new consulting company, with clients all over the world. The company provides management consulting to the travel industry.

Logo files are attached.

Website must look very corporate and be responsive in design.

Management Consulting

```html
<!DOCTYPE html>
<html lang="en">
<head>
<meta charset="utf-8">
<title>Brivane Strategy Management, Inc.</title>
<link href="https://fonts.googleapis.com/css2?family=Lato:ital,wght@0,400;0,700;1,700&family=Roboto:wght@400;500&display=swap" rel="stylesheet">
<style>
:root{
  --bg:#1d1b1a;
  --white:#ffffff;
  --green:#5cb52a;
  --green-dark:#4a9a1f;
  --blue:#1a6fc0;
  --blue-text:#1c74c9;
  --navy:#14254a;
  --ink:#2b2b2b;
  --grey:#7a7a7a;
  --grey-light:#e8e8e8;
  --grey-tab:#6f6f6f;
  --dark-badge:#1b1b1b;
}
*{margin:0;padding:0;box-sizing:border-box}
html,body{width:1200px;height:1048px;overflow:hidden}
body{position:relative;background:radial-gradient(ellipse at 50% 40%,#2c2927 0%,var(--bg) 70%);font-family:"Lato",sans-serif;color:var(--ink)}
.abs{position:absolute}
.side-art{position:absolute;width:150px;height:320px;background:radial-gradient(ellipse at center,#4b6f93 0%,#2a3a4c 45%,rgba(29,27,26,0) 75%)}
.side-art.left-top{left:-40px;top:0}
.side-art.right-bottom{right:-40px;top:690px}
.top-phone{left:806px;top:14px;display:flex;align-items:center;gap:8px;color:var(--white);font-size:20px;font-weight:700}
.top-phone .ico{width:30px;height:30px;border-radius:50%;background:var(--green);display:flex;align-items:center;justify-content:center}
.header{left:139px;top:40px;width:978px;height:92px}
.brand{left:168px;top:56px;display:flex;align-items:center;gap:12px}
.brand .mark{width:56px;height:56px;border-radius:50%;background:var(--blue)}
.brand .name{font-size:27px;font-weight:700;color:var(--navy);line-height:1}
.main-nav{left:0;top:54px;width:1200px;height:67px;font-size:19px;color:var(--navy)}
.nav-link{position:absolute;top:0;height:67px;display:flex;align-items:center;white-space:nowrap;color:inherit;text-decoration:none}
.nav-link.is-active{background:var(--green);color:var(--white);width:57px;justify-content:center}
.hero{left:139px;top:121px;width:923px;height:397px;background:linear-gradient(180deg,#0d3f94 0%,#2b7fd4 35%,#8dc3ec 60%,#dcebf5 80%,#f3f7fb 100%)}
.slide-btn{width:38px;height:38px;border-radius:50%;background:var(--white);box-shadow:0 2px 4px rgba(0,0,0,.4);display:flex;align-items:center;justify-content:center;top:289px}
.slide-btn.prev{left:120px}
.slide-btn.next{left:1038px}
.cta{left:493px;top:400px;height:33px;display:flex;background:var(--white);box-shadow:0 1px 3px rgba(0,0,0,.3)}
.cta .go{width:34px;background:var(--green);display:flex;align-items:center;justify-content:center}
.cta .label{padding:0 14px 0 12px;display:flex;align-items:center;font-style:italic;font-weight:700;font-size:17px;color:var(--navy)}
.content{left:139px;top:518px;width:923px;height:340px;background:var(--white)}
.service-band{left:205px;top:433px;width:790px;height:155px}
.service{position:absolute;top:453px;width:110px;text-align:center;font-size:15px;color:var(--ink)}
.service .disc{width:92px;height:92px;margin:0 auto 6px;border-radius:50%;background:radial-gradient(circle at 50% 35%,#9a9a9a,#5a5a5a);border:4px solid #d9d9d9;display:flex;align-items:center;justify-content:center;box-shadow:0 3px 4px rgba(0,0,0,.35)}
.service.current .disc{background:radial-gradient(circle at 50% 35%,#6fcf37,#3f8f18)}
.section-title{font-size:18px;color:var(--navy)}
.section-title span{color:var(--blue-text)}
.rule{height:10px}
.welcome{left:156px;top:607px;width:600px}
.welcome p{margin-top:12px;padding-left:4px;font-size:12px;line-height:17px;color:#333;width:606px}
.welcome p b{color:#111;font-size:11px}
.why{left:160px;top:718px;width:600px;height:118px;background:var(--green);box-shadow:0 4px 4px rgba(0,0,0,.25)}
.why .photo{position:absolute;left:12px;top:15px;width:133px;height:82px;border:2px solid #e7f3e0;background:linear-gradient(180deg,#d6dde3,#6d7680)}
.why h3{position:absolute;left:159px;top:13px;font-size:16px;font-weight:400;color:var(--white)}
.why p{position:absolute;left:159px;top:38px;width:430px;font-size:12px;line-height:16px;color:var(--white)}
.divider{left:775px;top:600px;width:1px;height:240px;background:#dcdcdc}
.news{left:794px;top:600px;width:248px}
.news-arrows{position:absolute;right:0;top:8px;display:flex;gap:2px}
.news-item{position:absolute;left:0;width:248px;height:60px}
.news-item .date{position:absolute;left:0;top:0;width:34px;text-align:center}
.news-item .day{background:var(--blue);color:var(--white);font-weight:700;font-size:18px;height:22px;line-height:22px}
.news-item .mon{background:var(--dark-badge);color:var(--white);font-size:10px;height:14px;line-height:14px}
.news-item h4{position:absolute;left:47px;top:-4px;font-family:"Roboto",sans-serif;font-weight:400;font-size:14px;color:#222}
.news-item p{position:absolute;left:47px;top:12px;font-family:"Roboto",sans-serif;font-size:13px;color:#333}
.news-item a{position:absolute;left:47px;top:30px;font-size:11px;font-weight:700;color:var(--blue-text);text-decoration:none}
.news-sep{position:absolute;left:0;width:248px;border-top:1px dashed #bdbdbd}
.clients{left:139px;top:858px;width:923px;height:98px;background:var(--grey-light)}
.clients-tab{left:552px;top:859px;width:120px;height:23px}
.clients-tab span{position:absolute;left:0;top:1px;width:120px;text-align:center;color:var(--white);font-size:17px}
.client{top:904px;font-size:22px;font-weight:700;color:#8c8c8c;display:flex;align-items:center;gap:6px}
.client i{display:block;width:16px;height:16px;border-radius:50%;background:#9a9a9a}
.footer-links{left:142px;top:978px;font-size:12px;font-weight:700;color:var(--white);display:flex;gap:12px}
.footer-links span.sep{font-weight:400}
.footer-contact{font-size:12px;color:var(--white);line-height:18px}
.subscribe{left:802px;top:973px;display:flex;height:33px}
.subscribe .field{width:170px;background:var(--white);display:flex;align-items:center;gap:8px;padding-left:10px;font-style:italic;font-size:11px;color:#9a9a9a}
.subscribe .btn{width:90px;background:var(--blue);color:var(--white);font-size:14px;font-weight:700;display:flex;align-items:center;justify-content:center;letter-spacing:.3px}
.bottom-bar{left:0;top:1020px;width:1200px;height:28px;background:var(--blue)}
.copyright{left:139px;top:1026px;font-size:12px;color:var(--white)}
.social{left:949px;top:1023px;display:flex;gap:5px}
.social i{display:block;width:22px;height:22px;border-radius:50%;border:1.5px solid var(--white)}
</style>
</head>
<body>
  <div class="side-art left-top" role="img" aria-label="Glowing globe of travel photographs"></div>
  <div class="side-art right-bottom" role="img" aria-label="Glowing globe of travel photographs"></div>

  <div class="abs top-phone">
    <span class="ico"><svg width="16" height="16" viewBox="0 0 24 24"><path fill="#fff" d="M6.6 10.8c1.4 2.8 3.8 5.1 6.6 6.6l2.2-2.2c.3-.3.7-.4 1-.2 1.1.4 2.3.6 3.6.6.6 0 1 .4 1 1V20c0 .6-.4 1-1 1C10.6 21 3 13.4 3 4c0-.6.4-1 1-1h3.5c.6 0 1 .4 1 1 0 1.3.2 2.5.6 3.6.1.3 0 .7-.2 1z"/></svg></span>
    123-456-7890
  </div>

  <svg class="abs header" viewBox="0 0 978 92" aria-hidden="true"><polygon points="0,14 918,14 918,0 978,38 918,92 918,81 0,81" fill="#fff"/></svg>

  <div class="abs brand">
    <span class="mark"></span>
    <span class="name">Brivane Management</span>
  </div>

  <nav class="abs main-nav">
    <a class="nav-link is-active" href="#" style="left:544px">Home</a>
    <a class="nav-link" href="#" style="left:636px">About Us</a>
    <a class="nav-link" href="#" style="left:749px">Our Services</a>
    <a class="nav-link" href="#" style="left:880px">Contact Us</a>
  </nav>

  <div class="abs hero" role="img" aria-label="Travel collage: airliner in a starry blue sky over snowy mountains with world landmarks and a skier"></div>

  <div class="abs slide-btn prev"><svg width="14" height="14" viewBox="0 0 14 14"><path d="M9 2 4 7l5 5" stroke="#333" stroke-width="2.6" fill="none"/></svg></div>
  <div class="abs slide-btn next"><svg width="14" height="14" viewBox="0 0 14 14"><path d="M5 2l5 5-5 5" stroke="#333" stroke-width="2.6" fill="none"/></svg></div>

  <div class="abs content"></div>

  <svg class="abs service-band" viewBox="0 0 790 155" aria-hidden="true">
    <polygon points="0,86 38,86 38,144" fill="#4e4e4e"/>
    <polygon points="790,86 752,86 752,144" fill="#4e4e4e"/>
    <polygon points="119,0 677,0 743,151 53,151" fill="#fff" style="filter:drop-shadow(0 3px 3px rgba(0,0,0,.25))"/>
  </svg>

  <div class="abs cta">
    <span class="go"><svg width="12" height="16" viewBox="0 0 12 16"><path d="M3 2l6 6-6 6" stroke="#fff" stroke-width="3" fill="none"/></svg></span>
    <span class="label">Get Started With Us !</span>
  </div>

  <div class="service current" style="left:323px">
    <div class="disc"><svg width="38" height="38" viewBox="0 0 24 24" fill="none" stroke="#fff" stroke-width="1.8"><rect x="4" y="4" width="13" height="16" rx="1"/><path d="M7 9h6M7 12h6M7 15h3M13 17l7-8"/></svg></div>Planning</div>
  <div class="service" style="left:433px">
    <div class="disc"><svg width="38" height="38" viewBox="0 0 24 24" fill="none" stroke="#fff" stroke-width="2"><path d="M5 5l14 14M19 5 9 15M5 19l3-3"/></svg></div>Development</div>
  <div class="service" style="left:546px">
    <div class="disc"><svg width="38" height="38" viewBox="0 0 24 24" fill="#fff"><rect x="5" y="11" width="3" height="8"/><rect x="10" y="6" width="3" height="13"/><rect x="15" y="9" width="3" height="10"/><rect x="3" y="19" width="18" height="1.5"/></svg></div>Analysis</div>
  <div class="service" style="left:659px">
    <div class="disc"><svg width="38" height="38" viewBox="0 0 24 24" fill="none" stroke="#fff" stroke-width="1.6"><circle cx="12" cy="12" r="8"/><path d="M4 12h16M12 4c3 3 3 13 0 16M12 4c-3 3-3 13 0 16"/></svg></div>Marketing</div>
  <div class="service" style="left:769px">
    <div class="disc"><svg width="38" height="38" viewBox="0 0 24 24" fill="none" stroke="#fff" stroke-width="1.8"><circle cx="12" cy="12" r="8"/><circle cx="12" cy="12" r="4.5"/><circle cx="12" cy="12" r="1.2" fill="#fff"/><path d="M12 12l7-7"/></svg></div>Solutions</div>

  <section class="abs welcome">
    <h2 class="section-title">Welcome to <span>Brivane Strategy Management, Inc.</span></h2>
    <svg class="rule" width="600" height="10" viewBox="0 0 600 10"><line x1="0" y1="5" x2="110" y2="5" stroke="#1c74c9" stroke-width="2"/><circle cx="110" cy="5" r="4" fill="#14254a"/><line x1="115" y1="5" x2="598" y2="5" stroke="#999" stroke-dasharray="4 3"/></svg>
    <p>Lorem ipsum dolor sit amet, consectetu adipiscing elit, sed diam nonummy nibh euismod tincidunt ut laoreet dolore magna aliquam erat volutpat.  wisi enim ad minim veniam, quisLorem ipsum dolor sit amet, consectetu adipiscing elit, sed diam ...<b>Read more</b></p>
  </section>

  <div class="abs why">
    <div class="photo" role="img" aria-label="Business team shaking hands in an office"></div>
    <h3>Why Choose Us</h3>
    <p>Lorem ipsum dolor sit amet, consectetu adipiscing elit, sed diam nonummy nibh euismod tincidunt ut laoreet dolore magna aliquam erat volutpat.  wisi enim ad minim veniam.</p>
  </div>

  <div class="abs divider"></div>

  <section class="abs news">
    <h2 class="section-title">News &amp; <span>Events</span></h2>
    <div class="news-arrows"><svg width="16" height="12" viewBox="0 0 16 12"><polygon points="6,1 1,6 6,11" fill="#5cb52a"/><polygon points="10,1 15,6 10,11" fill="#5cb52a"/></svg></div>
    <svg class="rule" width="248" height="10" viewBox="0 0 248 10" style="position:absolute;left:0;top:25px"><line x1="0" y1="5" x2="111" y2="5" stroke="#14254a" stroke-width="1.5"/><circle cx="111" cy="5" r="4" fill="#14254a"/><line x1="115" y1="5" x2="248" y2="5" stroke="#14254a" stroke-width="1.5"/></svg>

    <div class="news-item" style="top:54px">
      <div class="date"><div class="day">25</div><div class="mon">OCT</div></div>
      <h4>Start Talvina Website</h4><p>Lorem ipsum dolor sit amet ellit.</p><a href="#">Read More...</a>
    </div>
    <div class="news-sep" style="top:108px"></div>
    <div class="news-item" style="top:127px">
      <div class="date"><div class="day">25</div><div class="mon">OCT</div></div>
      <h4>Start Talvina Website</h4><p>Lorem ipsum dolor sit amet ellit.</p><a href="#">Read More...</a>
    </div>
    <div class="news-sep" style="top:181px"></div>
    <div class="news-item" style="top:200px">
      <div class="date"><div class="day">25</div><div class="mon">OCT</div></div>
      <h4>Start Talvina Website</h4><p>Lorem ipsum dolor sit amet ellit.</p><a href="#">Read More...</a>
    </div>
  </section>

  <div class="abs clients"></div>
  <div class="abs clients-tab">
    <svg width="120" height="23" viewBox="0 0 120 23" style="position:absolute;left:0;top:0"><polygon points="8,0 120,0 112,23 0,23" fill="#6f6f6f"/></svg>
    <span>Our Clients</span>
  </div>
  <div class="abs client" style="left:300px"><i></i>Ardeno</div>
  <div class="abs client" style="left:428px">Velto</div>
  <div class="abs client" style="left:548px">Quillon</div>
  <div class="abs client" style="left:678px">Marsette</div>
  <div class="abs client" style="left:826px">Hexlow</div>

  <div class="abs footer-links">
    <span>Home</span><span class="sep">|</span><span>About Us</span><span class="sep">|</span><span>Services</span><span class="sep">|</span><span>Contact Us</span>
  </div>
  <div class="abs footer-contact" style="left:436px;top:976px;display:flex;gap:10px">
    <svg width="12" height="14" viewBox="0 0 12 16" style="margin-top:3px"><path d="M6 0a6 6 0 0 0-6 6c0 4.5 6 10 6 10s6-5.5 6-10a6 6 0 0 0-6-6zm0 8.5A2.5 2.5 0 1 1 6 3.5a2.5 2.5 0 0 1 0 5z" fill="#fff"/></svg>
    <span>Lorem ipsum dolor sit amet,<br>consectetuer adimpisciged</span>
  </div>
  <div class="abs footer-contact" style="left:612px;top:976px">
    <div style="display:flex;align-items:center;gap:8px;font-size:13px"><svg width="12" height="12" viewBox="0 0 24 24"><path fill="#fff" d="M6.6 10.8c1.4 2.8 3.8 5.1 6.6 6.6l2.2-2.2c.3-.3.7-.4 1-.2 1.1.4 2.3.6 3.6.6.6 0 1 .4 1 1V20c0 .6-.4 1-1 1C10.6 21 3 13.4 3 4c0-.6.4-1 1-1h3.5c.6 0 1 .4 1 1 0 1.3.2 2.5.6 3.6.1.3 0 .7-.2 1z"/></svg>123-456-7890</div>
    <div style="display:flex;align-items:center;gap:6px;margin-top:3px"><svg width="11" height="9" viewBox="0 0 12 9"><rect width="12" height="9" fill="#fff"/><path d="M0 0l6 5 6-5" stroke="#1d1b1a" fill="none"/></svg>info@brivanestrategy.com</div>
  </div>

  <div class="abs subscribe">
    <div class="field"><svg width="14" height="10" viewBox="0 0 12 9"><rect x=".5" y=".5" width="11" height="8" fill="none" stroke="#bbb"/><path d="M.5.5l5.5 4.5 5.5-4.5" stroke="#bbb" fill="none"/></svg>your e-mail address</div>
    <div class="btn">SUBSCRIBE</div>
  </div>

  <div class="abs bottom-bar"></div>
  <div class="abs copyright">Copyright © 2014  Brivane Strategy.All Right Reserved</div>
  <div class="abs social"><i></i><i></i><i></i><i></i></div>
</body>
</html>
```